Bramblewood Joinery Website

My client Bramblewood Joinery is looking for a redesign for a Word Press Website. Their current site is at www.bramblewoodjoinery.example They are a custom cabinet company, but also create bathroom, living room, bar and entertainment and bedroom cabinets too. They would like a design that emulates the master craftsman work they do yet a contemporary style.

Their current site was designed using Flash elements.

Target Market(s)

Home owners and builders of high end homes

Industry/Entity Type

Entertainment

Font styles to use
Serif
Decorative

Requirements
Must have
• Must show their work and logo using a contemporary style.
Nice to have
• Sliders that showcase their projects.

```html
<!DOCTYPE html>
<html lang="en">
<head>
<meta charset="utf-8">
<title>Bramblewood Joinery</title>
<link href="https://fonts.googleapis.com/css2?family=Ubuntu:wght@400;500;700&display=swap" rel="stylesheet">
<style>
:root{
  --green:#2f9e33;
  --green-dark:#23802a;
  --ribbon:#2a8c2e;
  --ink:#222;
  --text:#666;
  --page:#f1f1f1;
  --footer:#262626;
  --tab:#262626;
  --footer-text:#aaa;
}
*{margin:0;padding:0;box-sizing:border-box}
html,body{width:999px;height:1200px;overflow:hidden}
body{position:relative;background:var(--page);font-family:"Ubuntu",sans-serif;color:var(--ink)}
.abs{position:absolute}

.backdrop{left:0;top:0;width:999px;height:466px;
  background:
    radial-gradient(ellipse 160px 220px at 60px 380px,rgba(120,120,120,.45),transparent),
    radial-gradient(ellipse 140px 200px at 940px 200px,rgba(150,150,150,.35),transparent),
    linear-gradient(180deg,#474747,#2f2f2f 60%,#1f1f1f)}

.sheet{left:134px;top:45px;width:731px;height:737px;background:#fff;border:1px solid #ddd;box-shadow:0 8px 10px -8px rgba(0,0,0,.35)}
.sheet-inner{left:140px;top:51px;width:719px;height:725px;border:1px solid #e3e3e3}

.ribbon-end{top:62px}
.nav{left:126px;top:58px;width:747px;height:44px;background:var(--green);box-shadow:0 2px 3px rgba(0,0,0,.25)}
.nav a{position:absolute;top:0;height:44px;line-height:44px;color:#fff;font-size:9px;text-decoration:none;text-transform:uppercase}
.nav .current{background:var(--tab);padding:0 14px;left:8px}
.brand{left:454px;top:30px;width:92px;height:92px;border-radius:50%;background:#fff;border:3px solid #222;display:flex;align-items:center;justify-content:center;text-align:center;font-size:11px;font-weight:700;color:var(--green);line-height:1.2}

.hero{left:151px;top:118px;width:697px;height:348px;
  background:
    radial-gradient(ellipse 200px 140px at 580px 150px,rgba(200,215,228,.9),transparent),
    radial-gradient(ellipse 260px 80px at 330px 300px,rgba(70,62,58,.75),transparent),
    linear-gradient(180deg,#e9e6e1 0%,#ddd8d0 45%,#c9c4bc 70%,#6a625c 88%,#4a4440 100%)}
.hero-sub{left:151px;top:232px;width:697px;text-align:center;font-size:26px;font-weight:500;color:#444;letter-spacing:.3px}
.hero-title{left:151px;top:267px;width:697px;text-align:center;font-size:42px;font-weight:700;color:#1d1d1d}
.btn{position:absolute;background:var(--green);color:#fff;text-transform:uppercase;text-align:center;font-weight:500;box-shadow:0 2px 0 var(--green-dark)}
.hero-btn{left:441px;top:318px;width:117px;height:34px;line-height:34px;font-size:11px}
.slider-nav{left:791px;top:409px;width:42px;height:42px}

.cat-title{position:absolute;font-size:12px;font-weight:500;top:482px;text-transform:uppercase}
.thumb{position:absolute;border:1px solid #ddd;padding:3px;background:#fff}
.fill{width:100%;height:100%}
.cat-text{position:absolute;top:665px;width:160px;font-size:8.5px;line-height:13px;color:var(--text)}
.cat-btn{top:730px;width:72px;height:29px;line-height:29px;font-size:8.5px}

.section-title{font-size:14px;font-weight:500;top:826px;text-transform:uppercase}
.about-lead{left:297px;top:877px;width:230px;font-size:12px;line-height:16px;color:var(--green)}
.about-text{left:297px;top:924px;width:220px;font-size:8.5px;line-height:13.5px;color:var(--text)}
.about-more{left:134px;top:1005px;width:390px;font-size:8.5px;line-height:13.5px;color:var(--text)}

.footer{left:0;top:1098px;width:999px;height:102px;background:var(--footer)}
.footer-title{position:absolute;top:1121px;font-size:11px;font-weight:400;color:#fff;text-transform:uppercase}
.footer-text{font-size:8.5px;line-height:16px;color:var(--footer-text)}
.footer-brand{left:136px;top:1120px;width:60px;height:60px;border-radius:50%;border:2px solid #3c3c3c;display:flex;align-items:center;justify-content:center;text-align:center;font-size:8px;font-weight:700;line-height:1.2;color:#4a4a4a}
.social{top:1146px;width:25px;height:25px;border-radius:50%}
</style>
</head>
<body>
<div class="abs backdrop" role="img" aria-label="Dim photo of a modern bathroom interior"></div>

<div class="abs sheet"></div>
<div class="abs sheet-inner"></div>

<svg class="abs ribbon-end" style="left:81px" width="50" height="48" viewBox="0 0 50 48"><polygon points="0,4 50,4 50,48 0,48 14,26" fill="#2a8c2e"/></svg>
<svg class="abs ribbon-end" style="left:868px" width="50" height="48" viewBox="0 0 50 48"><polygon points="0,4 50,4 36,26 50,48 0,48" fill="#2a8c2e"/></svg>

<nav class="abs nav">
  <a class="current" href="#">Home</a>
  <a href="#" style="left:78px">Who We Are</a>
  <a href="#" style="left:156px">Contact Us</a>
  <a href="#" style="left:232px">Customers</a>
  <a href="#" style="left:457px">Our Professional</a>
  <a href="#" style="left:564px">Portfolio</a>
  <a href="#" style="left:636px">Cabinet Hardware</a>
</nav>
<div class="abs brand">Bramblewood<br>Joinery</div>

<div class="abs hero" role="img" aria-label="Bright bathroom with dark wood vanity cabinets, pendant lights and lake view"></div>
<div class="abs hero-sub">WE ARE A CUSTOM</div>
<div class="abs hero-title">CABINET COMPANY</div>
<div class="btn hero-btn">Get Started</div>
<svg class="abs slider-nav" viewBox="0 0 42 42"><circle cx="21" cy="21" r="21" fill="#2f9e33"/><path d="M17 15l-5 6 5 6M25 15l5 6-5 6" stroke="#fff" stroke-width="2" fill="none"/><line x1="21" y1="12" x2="21" y2="30" stroke="#4cb84f"/></svg>

<section class="categories">
  <h3 class="cat-title" style="left:150px">Bathroom</h3>
  <h3 class="cat-title" style="left:333px">Living Room</h3>
  <h3 class="cat-title" style="left:508px">Bar &amp; Entertainment</h3>
  <h3 class="cat-title" style="left:686px">Bedroom Cabinets</h3>

  <div class="thumb" style="left:151px;top:506px;width:160px;height:145px"><div class="fill" role="img" aria-label="Bathroom with carved wood vanity and mirror" style="background:linear-gradient(180deg,#b89a70 0%,#9a7650 40%,#6a3e1e 65%,#4a2812 100%)"></div></div>
  <div class="thumb" style="left:330px;top:506px;width:160px;height:145px"><div class="fill" role="img" aria-label="Living room office with dark wall cabinets" style="background:linear-gradient(180deg,#e8e6e2 0%,#5a2e22 25%,#3e1c14 70%,#b8b6b2 100%)"></div></div>
  <div class="thumb" style="left:508px;top:506px;width:160px;height:145px"><div class="fill" role="img" aria-label="Warm wood bar and kitchen cabinets" style="background:linear-gradient(180deg,#7a4a20 0%,#c06a2a 35%,#a85020 65%,#5a2a10 100%)"></div></div>
  <div class="thumb" style="left:686px;top:506px;width:160px;height:145px"><div class="fill" role="img" aria-label="Bedroom built-in cabinets around a fireplace" style="background:linear-gradient(180deg,#d8d2c0 0%,#bdb6a4 40%,#6a6860 70%,#4a4a48 100%)"></div></div>

  <p class="cat-text" style="left:154px">Lorem ipsum dolor sit amet, cons ecte tadipiscing elit, sed do eiusmod tem porncid idunt ut labore et dolore magn aliq uat enim ad minim veniam.</p>
  <p class="cat-text" style="left:333px">Lorem ipsum dolor sit amet, cons ecte tadipiscing elit, sed do eiusmod tem porncid idunt ut labore et dolore magn aliq uat enim ad minim veniam.</p>
  <p class="cat-text" style="left:511px">Lorem ipsum dolor sit amet, cons ecte tadipiscing elit, sed do eiusmod tem porncid idunt ut labore et dolore magn aliq uat enim ad minim veniam.</p>
  <p class="cat-text" style="left:689px">Lorem ipsum dolor sit amet, cons ecte tadipiscing elit, sed do eiusmod tem porncid idunt ut labore et dolore magn aliq uat enim ad minim veniam.</p>

  <div class="btn cat-btn" style="left:153px">Read More</div>
  <div class="btn cat-btn" style="left:332px">Read More</div>
  <div class="btn cat-btn" style="left:510px">Read More</div>
  <div class="btn cat-btn" style="left:688px">Read More</div>
</section>

<h2 class="abs section-title" style="left:138px">About Our Company</h2>
<div class="thumb" style="left:134px;top:864px;width:141px;height:131px"><div class="fill" role="img" aria-label="Video still of a tall wood display cabinet" style="background:linear-gradient(90deg,#4a1a10 0%,#7a2a18 35%,#5a1e10 70%,#e4e0d8 100%)"></div></div>
<svg class="abs" style="left:190px;top:915px" width="30" height="30" viewBox="0 0 30 30"><circle cx="15" cy="15" r="13" fill="rgba(0,0,0,.3)" stroke="#fff" stroke-width="2"/><polygon points="12,9 21,15 12,21" fill="#fff"/></svg>
<div class="abs about-lead">Kansas City's Premier Custom Kitchen Cabinet Design Company</div>
<div class="abs about-text">At Bramblewood Joinery, we've been designing and manufacturing the Midwest's finest custom cabinets and fixtures since 1966. From single cabinets to room remodels to entire home installations, our expert</div>
<div class="abs about-more">Lorem ipsum dolor sit amet, cons ecte tadipiscing elit, sed do eiusmod tem porncid idunt ut la bore et dolore magn aliq uat enim ad minim veniam.sed do eiusmod tem porncid idunt ut labore Lorem ipsum dolor sit amet, cons ecte tadipisc.</div>

<h2 class="abs section-title" style="left:550px">Our Gallery</h2>
<div class="thumb" style="left:550px;top:863px;width:98px;height:86px"><div class="fill" role="img" aria-label="White kitchen with steel fridge" style="background:linear-gradient(90deg,#5a5e62 0%,#c8cacc 40%,#e8e6e0 70%,#8a8680 100%)"></div></div>
<div class="thumb" style="left:657px;top:863px;width:98px;height:86px"><div class="fill" role="img" aria-label="Wood display cabinet" style="background:linear-gradient(180deg,#5a2210 0%,#9a4a24 45%,#7a3418 100%)"></div></div>
<div class="thumb" style="left:764px;top:863px;width:98px;height:86px"><div class="fill" role="img" aria-label="Grey cabinet detail" style="background:linear-gradient(135deg,#d8d0c0 0%,#8a8a86 50%,#3e4650 100%)"></div></div>
<div class="thumb" style="left:550px;top:957px;width:98px;height:86px"><div class="fill" role="img" aria-label="Wood vanity drawers" style="background:linear-gradient(180deg,#c08a50 0%,#8a4a22 40%,#5a2a12 100%)"></div></div>
<div class="thumb" style="left:657px;top:957px;width:98px;height:86px"><div class="fill" role="img" aria-label="Black kitchen island" style="background:linear-gradient(90deg,#2a2a2a 0%,#141414 55%,#6a6a6a 85%,#3a3a3a 100%)"></div></div>
<div class="thumb" style="left:764px;top:957px;width:98px;height:86px"><div class="fill" role="img" aria-label="Light oak kitchen" style="background:linear-gradient(180deg,#8a5a2a 0%,#d8a868 35%,#c48c48 70%,#9a6430 100%)"></div></div>

<footer class="abs footer"></footer>
<div class="abs footer-brand">Bramblewood<br>Joinery</div>
<div class="abs footer-text" style="left:209px;top:1134px;color:#ccc">© 2015 Bramblewood Joinery<br>all rights are reserved</div>
<h4 class="footer-title" style="left:363px">Let's Talk</h4>
<h4 class="footer-title" style="left:518px">Find Us</h4>
<h4 class="footer-title" style="left:715px">Follow Us</h4>
<div class="abs footer-text" style="left:363px;top:1145px">Phone: 555.014.2300<br>Fax: 555.014.7835</div>
<div class="abs footer-text" style="left:518px;top:1145px">Bramblewood Joinery Marcus Hale<br>4820 Alder Lane Fairmont, MO 64000</div>
<div class="abs social" style="left:713px;background:#2aa3e0"></div>
<div class="abs social" style="left:745px;background:#f29a1f"></div>
<div class="abs social" style="left:776px;background:#3b5a9a"></div>
<div class="abs social" style="left:808px;background:#d8283a"></div>
<div class="abs social" style="left:839px;background:#555"></div>
<div class="abs footer-text" style="left:934px;top:1155px;color:#ccc">C4</div>
</body>
</html>
```